Vorelan.com Personal Trainer/Fitness Website

I want a website to market my personal training/Outdoor Bootcamp Class services, as well as to ditribute nutrivex. I need a logo as well I included an address for the Harbor Gales 1975 logo. I'd like Vorelan in place of Harbor Gales, and in Black and white, just different enough so I can't get sued by the PBL.
https://www.pictofind.example/imgres?imgurl=http%3A%2F%2Fwww.darnell-quibury.example%2Fwp-content%2Fuploads%2F2014%2F01%2Fgales_logo4.jpg&imgrefurl=http%3A%2F%2Fwww.darnell-quibury.example%2Fpbl-logo-redesigns-harbor-gales%2F&docid=_qkwzR7TBAgXpL&tbnid=m4tpU8KdOXjnRP%3A&w=600&h=450&client=ms-android-carrier&bih=512&biw=360&ved=0ahUKEwiRtpgyp9HMAhUTwGMKHRPMBWMQMwg6KBQwFA&iact=mrc&uact=8.
It should be about 5 pages 1. home 2. about 3. Services 4. Blog/Videos and programs 5. Contact.
http://www.dorvinfitness.example.uk/ is a website I like the style of.

Target Market(s)

Seattle area

Industry/Entity Type

Fitness

Coding

Coded - Design and coding required

Number of Pages Required

4 page

Font styles to use
Serif
Sans Serif

Requirements
Must have
• A minimal look
Nice to have
• A logo similar to the 1975 Harbor Galewinds Logo, with a Small Milo Brandt ripping his shirt open(with a picture of the logo on his shirt, picture within picture) to turn into Ironjaw in the center. Skyline is black, Background and small figure white(with black logo on shirt)

```html
<!DOCTYPE html>
<html lang="en">
<head>
<meta charset="utf-8">
<title>Vorelan – Personal Training &amp; Outdoor Bootcamp</title>
<link href="https://fonts.googleapis.com/css2?family=Lato:ital,wght@0,400;0,700;0,900;1,400&family=Roboto:wght@400;500;700&display=swap" rel="stylesheet">
<style>
:root{
  --green:#0a6b36;
  --green-dark:#06522a;
  --red:#e8141b;
  --black:#000;
  --ink:#1d1d1d;
  --footer:#262626;
  --footer-line:#3d3d3d;
  --white:#fff;
  --grey:#bdbdbd;
}
*{box-sizing:border-box;margin:0;padding:0}
html,body{width:1200px;height:2446px;overflow:hidden}
body{position:relative;font-family:'Roboto',Arial,sans-serif;background:var(--white);color:var(--ink)}
.abs{position:absolute}

/* header */
.site-header{position:absolute;top:0;left:0;width:1200px;height:134px;background:#fdfdfd;border-top:3px solid #111}
.brand{position:absolute;left:82px;top:40px;display:flex;align-items:center;gap:12px}
.brand-dot{width:30px;height:30px;border-radius:50%;background:var(--red)}
.brand-name{font-family:'Lato',sans-serif;font-weight:900;font-size:34px;color:var(--green);letter-spacing:1px}
.join-btn{position:absolute;left:905px;top:23px;width:215px;height:44px;background:var(--red);color:#fff;border-radius:5px;font:500 21px 'Roboto',sans-serif;display:flex;align-items:center;justify-content:center;letter-spacing:.5px}
.header-contact{position:absolute;left:852px;top:83px;display:flex;align-items:center;gap:10px}
.ring-icon{width:32px;height:32px;border-radius:50%;background:var(--green);display:flex;align-items:center;justify-content:center}
.header-phone{font:700 21px 'Roboto',sans-serif;color:#111;margin-right:4px}
.social-dot{width:30px;height:30px;border-radius:50%}

/* nav */
.main-nav{position:absolute;top:134px;left:0;width:1200px;height:46px;background:var(--green)}
.main-nav ul{list-style:none;display:flex;position:absolute;left:82px;top:0;height:46px}
.main-nav li{height:46px;display:flex;align-items:center;justify-content:center;font:500 14px 'Roboto',sans-serif;color:#fff;letter-spacing:1px;border-right:1px solid rgba(255,255,255,.25)}
.main-nav li.active{background:var(--black)}

/* hero */
.hero{position:absolute;top:180px;left:0;width:1200px;height:620px;background:linear-gradient(180deg,#dfe8ee 0%,#c9d8c0 28%,#5d8a3a 48%,#6f9a3e 70%,#54772f 100%)}
.hero-arrow{position:absolute;top:290px}
.hero-title{position:absolute;top:480px;left:0;width:1200px;text-align:center;font:700 42px 'Lato',sans-serif;color:#fff;text-shadow:0 2px 6px rgba(0,0,0,.6);letter-spacing:.5px}
.hero-btn{position:absolute;left:522px;top:542px;width:156px;height:43px;border-radius:22px;background:var(--green);color:#fff;font:500 20px 'Roboto',sans-serif;display:flex;align-items:center;justify-content:center}

/* about */
.about{position:absolute;top:800px;left:0;width:1200px;height:281px;background:var(--black);color:#fff;text-align:center}
.section-title{font:700 26px 'Roboto',sans-serif;letter-spacing:.5px}
.about .section-title{position:absolute;top:38px;width:100%}
.about p{position:absolute;top:90px;left:80px;width:1040px;font:400 15px/24px 'Roboto',sans-serif}
.pill{position:absolute;background:var(--green);color:#fff;border-radius:15px;font:700 12px 'Roboto',sans-serif;display:flex;align-items:center;justify-content:center;letter-spacing:.5px}

/* services */
.services{position:absolute;top:1081px;left:0;width:1200px;height:435px;background:linear-gradient(120deg,#5e5e5e,#7c7b78 45%,#6a6866 70%,#55524f);color:#fff;text-align:center}
.services .section-title{position:absolute;top:60px;width:100%}
.rule{position:absolute;left:562px;width:76px;height:3px;background:var(--red)}
.services .sub{position:absolute;top:142px;width:100%;font:400 18px 'Lato',sans-serif;letter-spacing:.5px}
.service{position:absolute;top:210px;width:276px;margin-left:-138px;text-align:center}
.service-icon{width:118px;height:118px;border-radius:50%;background:var(--green);border:6px solid #d7d7d7;margin:0 auto;display:flex;align-items:center;justify-content:center}
.service-name{margin-top:26px;font:700 16px 'Roboto',sans-serif}

/* reviews */
.reviews{position:absolute;top:1516px;left:0;width:1200px;height:421px;background:#fff;text-align:center}
.reviews .section-title{position:absolute;top:46px;width:100%;color:var(--green)}
.review-box{position:absolute;left:80px;top:132px;width:1040px;height:174px;border:1px solid #ddd;border-radius:8px;box-shadow:0 1px 4px rgba(0,0,0,.12);background:#fff}
.review-box p{position:absolute;left:30px;top:22px;width:980px;font:italic 400 16px/25px 'Lato',sans-serif;color:#222;text-align:center}
.quote-mark{position:absolute;font:700 48px 'Lato',serif;color:#c8c8c8;line-height:1}
.bubble-tail{position:absolute;left:512px;top:305px}
.stars{position:absolute;left:355px;top:332px;display:flex;gap:6px}
.reviewer{position:absolute;left:355px;top:362px;font:400 15px 'Roboto',sans-serif;color:var(--green)}
.reviewer b{font-weight:700}

/* footer */
.site-footer{position:absolute;top:1937px;left:0;width:1200px;height:460px;background:var(--footer);color:#fff}
.newsletter{position:absolute;left:80px;top:55px;width:760px;height:70px;border:1px solid #1c5a37;border-radius:3px}
.newsletter-label{position:absolute;left:50px;top:22px;font:500 20px 'Roboto',sans-serif}
.newsletter-input{position:absolute;left:256px;top:17px;width:384px;height:36px;background:#fff;color:#333;font:400 13px 'Roboto',sans-serif;padding:10px 12px}
.newsletter-btn{position:absolute;left:640px;top:17px;width:100px;height:36px;background:var(--green);font:500 13px 'Roboto',sans-serif;display:flex;align-items:center;justify-content:center}
.follow{position:absolute;left:888px;top:76px;font:500 20px 'Roboto',sans-serif;display:flex;align-items:center;gap:12px}
.col-title{position:absolute;font:500 19px 'Roboto',sans-serif;display:flex;align-items:center;gap:10px}
.col-rule{position:absolute;height:2px;background:#555}
.field{position:absolute;border:1px solid #aaa;border-radius:3px;font:400 13px 'Roboto',sans-serif;color:#eee;padding:10px 12px}
.submit{position:absolute;left:323px;top:350px;width:226px;height:39px;background:var(--green);font:700 14px 'Roboto',sans-serif;display:flex;align-items:center;justify-content:center;letter-spacing:.5px}
.vline{position:absolute;top:160px;width:1px;height:230px;background:var(--footer-line)}
.quick-links{position:absolute;left:628px;top:220px;list-style:none}
.quick-links li{height:29px;font:400 13px 'Roboto',sans-serif;letter-spacing:.5px;display:flex;align-items:center;gap:10px}
.contact-line{position:absolute;left:866px;display:flex;align-items:center;gap:12px}
.footer-brand{position:absolute;left:866px;top:352px;display:flex;align-items:center;gap:10px}
.footer-brand span{font:900 28px 'Lato',sans-serif;color:var(--green);letter-spacing:1px}

.copyright{position:absolute;top:2397px;left:0;width:1200px;height:49px;background:#161616;border-top:2px solid var(--red);color:#fff;font:400 13px 'Roboto',sans-serif;text-align:center;line-height:46px}
</style>
</head>
<body>

<header class="site-header">
  <div class="brand"><div class="brand-dot"></div><div class="brand-name">VORELAN</div></div>
  <div class="join-btn">JOIN A SESSION</div>
  <div class="header-contact">
    <div class="ring-icon"><svg width="16" height="16" viewBox="0 0 24 24"><path fill="#fff" d="M6.6 10.8a15 15 0 0 0 6.6 6.6l2.2-2.2c.3-.3.7-.4 1-.2 1.1.4 2.3.6 3.6.6.6 0 1 .4 1 1V20c0 .6-.4 1-1 1A17 17 0 0 1 3 4c0-.6.4-1 1-1h3.5c.6 0 1 .4 1 1 0 1.3.2 2.5.6 3.6.1.3 0 .7-.2 1z"/></svg></div>
    <div class="header-phone">555-014-2318</div>
    <div class="social-dot" style="background:#1d5fa5"></div>
    <div class="social-dot" style="background:#8a6a4e"></div>
  </div>
</header>

<nav class="main-nav">
  <ul>
    <li class="active" style="width:133px">HOME</li>
    <li style="width:135px">ABOUT</li>
    <li style="width:160px">SERVICES</li>
    <li style="width:131px">BLOG</li>
    <li style="width:143px">VIDEOS</li>
    <li style="width:173px">PROGRAMS</li>
    <li style="width:161px">CONTACT</li>
  </ul>
</nav>

<section class="hero" role="img" aria-label="Photo of a man training with battle ropes and a woman throwing a medicine ball in a sunny park">
  <svg class="hero-arrow" style="left:28px" width="22" height="40" viewBox="0 0 22 40"><path d="M20 2 3 20l17 18" fill="none" stroke="rgba(255,255,255,.7)" stroke-width="2"/></svg>
  <svg class="hero-arrow" style="left:1150px" width="22" height="40" viewBox="0 0 22 40"><path d="M2 2l17 18L2 38" fill="none" stroke="rgba(255,255,255,.7)" stroke-width="2"/></svg>
  <h1 class="hero-title">GET FIT AND HAVE FUN THE WAY IT SHOULD BE</h1>
  <div class="hero-btn">CONTACT US</div>
</section>

<section class="about">
  <h2 class="section-title">ABOUT VORELAN</h2>
  <p>Lorem ipsum dolor sit amet, consectetuer adipiscing elit, sed diam nonummy nibh euismod tincidunt ut laoreet dolore magna aliquam erat sit volutpat. Ut wisi enim ad minim veniam, quis nostrud exerci tation ullamcorper suscipit lobortis nisl ut aliquip ex ea commodo consequat. Duis autem vel eum iriure dolor in hendrerit in vulputate velit esse molestie consequat, vel illum dolore eu feugiat nulla facilisis at vero eros et sit accumsan et iusto odio dignissim qui blandit praesent luptatum zzril delenit augue duis dolore te feugait nulla facilisi.</p>
  <div class="pill" style="left:546px;top:209px;width:106px;height:28px">READ MORE</div>
</section>

<section class="services" role="img" aria-label="Faded photo of a group stretching in a fitness class">
  <h2 class="section-title">OUR SERVICES</h2>
  <div class="rule" style="top:116px"></div>
  <div class="sub">SELECT TO LEARN MORE!</div>
  <div class="service" style="left:184px">
    <div class="service-icon"><svg width="54" height="54" viewBox="0 0 54 54"><rect x="4" y="19" width="8" height="16" rx="2" fill="#fff"/><rect x="42" y="19" width="8" height="16" rx="2" fill="#fff"/><rect x="12" y="24" width="30" height="6" fill="#fff"/></svg></div>
    <div class="service-name">PERSONAL TRAINING</div>
  </div>
  <div class="service" style="left:460px">
    <div class="service-icon"><svg width="60" height="54" viewBox="0 0 60 54"><circle cx="12" cy="16" r="6" fill="#fff"/><circle cx="30" cy="14" r="6" fill="#fff"/><circle cx="48" cy="16" r="6" fill="#fff"/><rect x="6" y="25" width="12" height="20" rx="3" fill="#fff"/><rect x="24" y="23" width="12" height="22" rx="3" fill="#fff"/><rect x="42" y="25" width="12" height="20" rx="3" fill="#fff"/></svg></div>
    <div class="service-name">OUTDOOR BOOTCAMP CLASSES</div>
  </div>
  <div class="service" style="left:735px">
    <div class="service-icon"><svg width="56" height="54" viewBox="0 0 56 54"><path d="M6 27h36" stroke="#fff" stroke-width="6"/><path d="M32 14l16 13-16 13" fill="none" stroke="#fff" stroke-width="6"/></svg></div>
    <div class="service-name">OUTDOOR GROUP TRAINING</div>
  </div>
  <div class="service" style="left:1011px">
    <div class="service-icon"><svg width="56" height="54" viewBox="0 0 56 54"><rect x="6" y="8" width="44" height="30" rx="2" fill="none" stroke="#fff" stroke-width="4"/><rect x="22" y="40" width="12" height="4" fill="#fff"/><rect x="16" y="44" width="24" height="3" fill="#fff"/></svg></div>
    <div class="service-name">ONLINE COACHING</div>
  </div>
</section>

<section class="reviews">
  <h2 class="section-title">CLIENT REVIEWS</h2>
  <div class="rule" style="top:102px"></div>
  <div class="review-box">
    <span class="quote-mark" style="left:26px;top:14px">&ldquo;</span>
    <p>I have been training with Darian for just a few weeks now and am already feeling a difference between this and past efforts to get healthy. He's exactly what I was looking for- someone who has been where I am and knows what it's like to have to work hard to lose the weight and learn what it takes to get healthy. From his comprehensive initial assessment (and I mean comprehensive- you will work!) to a customized training plan (not off the shelf- it's what your specific body needs) and great group classes, Darian offers it all. I get both the 1:1 attention and the energy from being with other folks in a class.</p>
    <span class="quote-mark" style="left:700px;top:130px">&rdquo;</span>
  </div>
  <svg class="bubble-tail" width="36" height="42" viewBox="0 0 36 42"><path d="M1 0v40L35 0" fill="#fff" stroke="#ddd"/><rect x="2" y="0" width="32" height="2" fill="#fff"/></svg>
  <div class="stars">
    <svg width="116" height="18" viewBox="0 0 116 18"><g fill="#aaa"><path id="st" d="M9 0l2.6 6 6.4.5-4.9 4.2 1.5 6.3L9 13.6 3.4 17l1.5-6.3L0 6.5 6.4 6z"/><use href="#st" x="24"/><use href="#st" x="48"/><use href="#st" x="72"/></g><use href="#st" x="96" fill="#666"/></svg>
  </div>
  <div class="reviewer"><b>Ravi T.</b> on March 20, 2016</div>
</section>

<footer class="site-footer">
  <div class="newsletter">
    <svg class="abs" style="left:14px;top:22px" width="26" height="24" viewBox="0 0 26 24"><path d="M2 9l11-7 11 7v13H2z" fill="#777"/><path d="M2 9l11 7 11-7" fill="none" stroke="#262626" stroke-width="2"/></svg>
    <div class="newsletter-label">NEWSLETTER SIGNUP</div>
    <div class="newsletter-input">Enter your email here</div>
    <div class="newsletter-btn">SUBSCRIBE</div>
  </div>
  <div class="follow">FOLLOW US <span class="social-dot" style="background:#1d5fa5;display:inline-block"></span><span class="social-dot" style="background:#8a6a4e;display:inline-block"></span></div>

  <div class="col-title" style="left:80px;top:163px"><svg width="26" height="26" viewBox="0 0 26 26"><circle cx="13" cy="13" r="11.5" fill="none" stroke="#888" stroke-width="2"/><text x="13" y="18" font-size="14" text-anchor="middle" fill="#888" font-family="Roboto,sans-serif" font-weight="700">?</text></svg>QUICK INQUIRY</div>
  <div class="col-rule" style="left:80px;top:202px;width:165px"></div>
  <div class="field" style="left:80px;top:234px;width:226px;height:39px">Name</div>
  <div class="field" style="left:323px;top:234px;width:231px;height:96px">Message</div>
  <div class="field" style="left:80px;top:291px;width:226px;height:39px">Email Address</div>
  <div class="field" style="left:80px;top:350px;width:226px;height:39px">Phone Number</div>
  <div class="submit">SUBMIT</div>

  <div class="vline" style="left:590px"></div>
  <div class="col-title" style="left:628px;top:170px"><svg width="20" height="24" viewBox="0 0 20 24"><rect x="1" y="3" width="18" height="20" rx="2" fill="none" stroke="#888" stroke-width="2"/><rect x="6" y="0" width="8" height="5" fill="#888"/></svg>QUICK LINKS</div>
  <div class="col-rule" style="left:628px;top:208px;width:170px"></div>
  <ul class="quick-links">
    <li><span>›</span>HOME</li><li><span>›</span>ABOUT</li><li><span>›</span>SERVICES</li><li><span>›</span>BLOG</li><li><span>›</span>VIDEOS</li><li><span>›</span>PROGRAMS</li><li><span>›</span>CONTACT</li>
  </ul>
  <div class="vline" style="left:831px"></div>

  <div class="col-title" style="left:866px;top:170px"><svg width="24" height="24" viewBox="0 0 24 24"><circle cx="12" cy="12" r="10" fill="none" stroke="#888" stroke-width="2"/><path d="M2 12h20M12 2c-5 5-5 15 0 20M12 2c5 5 5 15 0 20" fill="none" stroke="#888" stroke-width="1.5"/></svg>CONTACT DETAILS</div>
  <div class="col-rule" style="left:866px;top:208px;width:210px"></div>
  <div class="contact-line" style="top:230px"><div class="ring-icon" style="border:2px solid #fff"><svg width="14" height="14" viewBox="0 0 24 24"><path fill="#fff" d="M6.6 10.8a15 15 0 0 0 6.6 6.6l2.2-2.2c.3-.3.7-.4 1-.2 1.1.4 2.3.6 3.6.6.6 0 1 .4 1 1V20c0 .6-.4 1-1 1A17 17 0 0 1 3 4c0-.6.4-1 1-1h3.5c.6 0 1 .4 1 1 0 1.3.2 2.5.6 3.6.1.3 0 .7-.2 1z"/></svg></div><span style="font:500 19px 'Roboto',sans-serif">555-019-4470</span></div>
  <div class="contact-line" style="top:276px"><div class="ring-icon" style="border:2px solid #fff"><svg width="16" height="12" viewBox="0 0 16 12"><rect x="0.5" y="0.5" width="15" height="11" fill="none" stroke="#fff"/><path d="M1 1l7 6 7-6" fill="none" stroke="#fff"/></svg></div><span style="font:400 15px 'Roboto',sans-serif">info@vorelan.com</span></div>
  <div class="footer-brand"><div class="brand-dot" style="width:24px;height:24px"></div><span>VORELAN</span></div>
</footer>

<div class="copyright">
  <svg class="abs" style="left:588px;top:-12px" width="24" height="12" viewBox="0 0 24 12"><path d="M0 12L12 0l12 12z" fill="#e8141b"/></svg>
  COPYRIGHT 2016 © VORELAN All Rights Reserved • Privacy Policy • Terms of Use
</div>

</body>
</html>
```